Carpet cleaning company focused on high quality needs business cards

We are a growing company that just merged with another company and need to design a new business card. We do both residential as well as commercial cleaning. We do carpet, tile & grout, upholstery, hard floors, and stain & pet odor removal. We treat our customers like family and strive to achieve outstanding results with every job.

```html
<!DOCTYPE html>
<html lang="en">
<head>
<meta charset="UTF-8">
<title>Brightway Steam Care – Business Cards</title>
<link href="https://fonts.googleapis.com/css2?family=Open+Sans:wght@400;600;700;800&display=swap" rel="stylesheet">
<style>
  :root {
    --blue: #0a7fc2;
    --red: #ee4036;
    --ink: #111111;
    --paper: #ffffff;
    --backdrop: #d9dadc;
    --shadow: rgba(0,0,0,0.28);
  }
  * { margin: 0; padding: 0; box-sizing: border-box; }
  html, body {
    width: 1200px; height: 780px; overflow: hidden;
    background: linear-gradient(180deg, #cfd0d2 0%, #e4e5e7 100%);
    font-family: "Open Sans", Arial, sans-serif;
  }
  .stage {
    position: relative; width: 1200px; height: 780px;
    display: flex; align-items: center; justify-content: center; gap: 40px;
  }
  .card {
    position: relative; width: 540px; height: 309px;
    background: var(--paper);
    box-shadow: 0 10px 24px var(--shadow);
    overflow: hidden;
  }

  /* ---------- front: contact side ---------- */
  .brand {
    display: flex; align-items: center; gap: 12px;
  }
  .brand-square {
    width: 44px; height: 44px; background: var(--red); flex: none;
  }
  .brand-name {
    font-weight: 800; color: var(--ink); line-height: 1.02;
    text-transform: uppercase; letter-spacing: -0.3px;
  }
  .card-front .brand { position: absolute; left: 36px; top: 84px; }
  .card-front .brand-name { font-size: 22px; }
  .divider {
    position: absolute; left: 250px; top: 52px; width: 1px; height: 120px;
    background: var(--ink);
  }
  .contact { position: absolute; left: 272px; top: 46px; }
  .person-name { font-size: 27px; font-weight: 700; color: var(--blue); line-height: 1.1; }
  .person-name .surname { color: var(--red); }
  .person-role { font-size: 13px; color: var(--ink); margin-bottom: 14px; }
  .contact-list { list-style: none; }
  .contact-list li {
    display: flex; align-items: center; gap: 8px;
    font-size: 13px; color: var(--ink); line-height: 1.75;
  }
  .contact-list svg { width: 13px; height: 13px; flex: none; }
  .address-band { position: absolute; left: 0; bottom: 0; width: 540px; height: 140px; }
  .address {
    position: absolute; right: 26px; bottom: 20px;
    font-size: 13px; color: var(--paper); letter-spacing: 0.2px;
  }

  /* ---------- back: services side ---------- */
  .card-back .brand { position: absolute; left: 50%; top: 58px; transform: translateX(-50%); gap: 18px; }
  .card-back .brand-square { width: 96px; height: 96px; }
  .card-back .brand-name { font-size: 34px; }
  .services-heading {
    position: absolute; left: 40px; right: 40px; top: 192px;
    display: flex; align-items: center; gap: 10px;
    font-size: 13px; font-weight: 700; color: var(--red); white-space: nowrap;
  }
  .services-heading::before, .services-heading::after {
    content: ""; flex: 1; height: 1px; background: var(--red);
  }
  .services {
    position: absolute; left: 20px; right: 20px; top: 218px;
    list-style: none; text-align: center; font-size: 13.5px; color: var(--ink); line-height: 1.75;
  }
  .services li { display: inline; margin: 0 5px; }
  .services li::before {
    content: ""; display: inline-block; width: 7px; height: 7px; border-radius: 50%;
    background: var(--red); margin-right: 5px; vertical-align: middle;
  }
  .services .line-break { display: block; height: 0; }
</style>
</head>
<body>
<main class="stage">

  <section class="card card-front" aria-label="Business card, contact side">
    <div class="brand">
      <span class="brand-square"></span>
      <span class="brand-name">Brightway<br>Steam Care</span>
    </div>
    <span class="divider"></span>
    <div class="contact">
      <p class="person-name">Marta <span class="surname">Kovacs</span></p>
      <p class="person-role">Managing Director</p>
      <ul class="contact-list">
        <li>
          <svg viewBox="0 0 24 24"><path fill="var(--blue)" d="M6.6 10.8a15.1 15.1 0 0 0 6.6 6.6l2.2-2.2a1 1 0 0 1 1-.25 11.4 11.4 0 0 0 3.6.57 1 1 0 0 1 1 1V20a1 1 0 0 1-1 1A17 17 0 0 1 3 4a1 1 0 0 1 1-1h3.5a1 1 0 0 1 1 1c0 1.25.2 2.45.57 3.57a1 1 0 0 1-.25 1z"/></svg>
          (555) 214-6083
        </li>
        <li>
          <svg viewBox="0 0 24 24"><rect x="2" y="5" width="20" height="14" rx="2" fill="var(--blue)"/><path d="M3 6l9 7 9-7" stroke="#fff" stroke-width="2" fill="none"/></svg>
          hello@brightwaysteam.com
        </li>
        <li>
          <svg viewBox="0 0 24 24"><circle cx="12" cy="12" r="10" fill="var(--blue)"/><path d="M2 12h20M12 2c3 3 3 17 0 20M12 2c-3 3-3 17 0 20" stroke="#fff" stroke-width="1.5" fill="none"/></svg>
          www.brightwaysteam.com
        </li>
      </ul>
    </div>
    <svg class="address-band" viewBox="0 0 540 140" preserveAspectRatio="none" aria-hidden="true">
      <path d="M0 140 C 180 120, 330 80, 540 0 L540 140 Z" fill="var(--red)"/>
      <path d="M0 140 C 190 126, 340 88, 540 8 L540 140 Z" fill="var(--blue)"/>
    </svg>
    <p class="address">418 Harlow Ave. Suite 120 Cedar Ridge, TX 75000</p>
  </section>

  <section class="card card-back" aria-label="Business card, services side">
    <div class="brand">
      <span class="brand-square"></span>
      <span class="brand-name">Brightway<br>Steam Care</span>
    </div>
    <p class="services-heading">OUR SERVICES</p>
    <ul class="services">
      <li>Both residential as well as commercial cleaning</li>
      <span class="line-break"></span>
      <li>Carpet</li><li>Tile &amp; grout</li><li>Upholstery</li><li>Hard floors</li>
      <span class="line-break"></span>
      <li>Stain &amp; pet odor removal</li>
    </ul>
  </section>

</main>
</body>
</html>
```